Opening a Hair Salon

Looking for a design for my sign that looks high end, an emphasis on color but welcoming to men and women.

The name is Corvane Haircuts and Colors

Trying capture a more affluent client. Looking for a very modern look.

Reason: Time is going to quick and would like to see a few more options.

```html
<!DOCTYPE html>
<html lang="en">
<head>
<meta charset="utf-8">
<title>Corvane Haircuts and Colors – Salon Signs</title>
<link rel="stylesheet" href="https://fonts.googleapis.com/css2?family=Montserrat:wght@600;700;800&family=Oswald:wght@600;700&display=swap">
<style>
  :root{
    --stage-top:#2b4f78;
    --stage-bottom:#0c1522;
    --sign-light:#f4f3f5;
    --sign-grey:#e4e3e6;
    --magenta:#e0169c;
    --plum:#6b1a5a;
    --ink:#1d1a22;
    --teal:#17a4b2;
    --teal-deep:#12707b;
    --hair:#8a5a3c;
    --skin:#e2b59a;
    --shirt:#5f86b0;
  }
  *{margin:0;padding:0;box-sizing:border-box}
  html,body{width:1200px;height:679px;overflow:hidden}
  body{
    background:radial-gradient(ellipse at 50% 0%,var(--stage-top),var(--stage-bottom) 85%);
    font-family:"Montserrat",Arial,sans-serif;
    position:relative;
  }
  .sign{position:absolute;overflow:hidden;box-shadow:0 10px 24px rgba(0,0,0,.45);border:3px solid #fff}

  /* 8x2 sign */
  .sign--wide{left:65px;top:62px;width:1070px;height:270px;
    background:linear-gradient(90deg,var(--sign-light),var(--sign-grey))}
  .sign--wide .cta{position:absolute;left:40px;top:26px;font-weight:700;font-size:19px;color:var(--ink);letter-spacing:.3px}
  .sign--wide .phone{position:absolute;left:38px;top:46px;font-family:"Oswald",Arial,sans-serif;font-weight:700;
    font-size:62px;line-height:1;color:var(--magenta);-webkit-text-stroke:2px var(--ink);letter-spacing:1px}
  .contacts{position:absolute;left:50px;top:168px;list-style:none}
  .contacts li{display:flex;align-items:center;gap:10px;font-weight:700;font-size:17px;color:var(--plum);height:28px}
  .contacts svg{width:16px;height:16px;flex:none}
  .sign--wide .brand{position:absolute;left:385px;top:92px}

  .brand{display:flex;align-items:center;gap:12px}
  .brand-dot{width:52px;height:52px;border-radius:50%;background:var(--magenta);flex:none}
  .brand-name{font-weight:700;color:var(--plum);line-height:1.05;font-size:40px}
  .brand-name span{display:block;font-size:16px;letter-spacing:1px;text-transform:uppercase}

  .photo{position:absolute}
  .sign--wide .photo{left:690px;top:0;width:330px;height:264px;
    background:linear-gradient(90deg,var(--hair) 0%,var(--skin) 30%,#f1ede9 50%,var(--skin) 70%,var(--shirt) 100%)}
  .swoosh{position:absolute;inset:0;width:100%;height:100%}

  /* 10x2 sign */
  .sign--long{left:90px;top:398px;width:970px;height:196px;
    background:linear-gradient(90deg,var(--sign-grey),var(--sign-light) 60%,var(--sign-grey))}
  .sign--long .brand{position:absolute;left:30px;top:62px}
  .tagline{position:absolute;left:320px;top:22px;font-weight:800;font-size:23px;color:var(--teal-deep);line-height:1.25;letter-spacing:.5px}
  .tagline span{display:block;padding-left:58px}
  .sign--long .cta{position:absolute;left:368px;top:108px;font-family:"Oswald",Arial,sans-serif;font-weight:600;font-size:20px;color:var(--ink)}
  .sign--long .phone{position:absolute;left:366px;top:130px;font-family:"Oswald",Arial,sans-serif;font-weight:700;
    font-size:46px;line-height:1;color:var(--teal);-webkit-text-stroke:2px var(--ink);letter-spacing:1px}
  .sign--long .photo{left:690px;top:0;width:260px;height:190px;
    background:linear-gradient(90deg,var(--hair) 0%,var(--skin) 32%,#eeeae6 52%,var(--skin) 72%,var(--shirt) 100%)}
</style>
</head>
<body>

<section class="sign sign--wide" aria-label="8 by 2 salon sign">
  <div class="photo" role="img" aria-label="Photo of a woman with long straight brown hair and a man with a textured short haircut"></div>
  <svg class="swoosh" viewBox="0 0 1064 264" preserveAspectRatio="none" aria-hidden="true">
    <path d="M980 0 H1064 V264 H1040 C1060 170 1040 60 980 0Z" fill="var(--magenta)"/>
    <path d="M640 264 C720 220 820 230 900 264Z" fill="var(--magenta)" opacity=".85"/>
    <path d="M700 264 C780 240 840 248 880 264Z" fill="var(--plum)" opacity=".7"/>
  </svg>
  <p class="cta">MAKE AN APPOINTMENT TODAY!</p>
  <p class="phone">555-0142-678</p>
  <ul class="contacts">
    <li><svg viewBox="0 0 16 16"><circle cx="8" cy="8" r="7" fill="none" stroke="var(--magenta)" stroke-width="2"/><path d="M1 8h14M8 1c3 3 3 11 0 14M8 1c-3 3-3 11 0 14" fill="none" stroke="var(--magenta)" stroke-width="1.4"/></svg>WWW.CORVANESALON.COM</li>
    <li><svg viewBox="0 0 16 16"><circle cx="8" cy="8" r="8" fill="var(--magenta)"/><rect x="4" y="5.5" width="8" height="5" fill="none" stroke="#fff" stroke-width="1.2"/><path d="M4 5.5l4 3 4-3" fill="none" stroke="#fff" stroke-width="1.2"/></svg>HELLO@CORVANESALON.COM</li>
    <li><svg viewBox="0 0 16 16"><circle cx="8" cy="8" r="8" fill="var(--magenta)"/></svg>@CORVANESALON</li>
  </ul>
  <div class="brand">
    <div class="brand-dot"></div>
    <p class="brand-name">Corvane<span>Haircuts &amp; Colors</span></p>
  </div>
</section>

<section class="sign sign--long" aria-label="10 by 2 salon sign">
  <svg class="swoosh" viewBox="0 0 964 190" preserveAspectRatio="none" aria-hidden="true">
    <path d="M0 0 H250 C150 10 60 40 0 80Z" fill="var(--teal)"/>
    <path d="M0 0 H170 C100 12 40 30 0 55Z" fill="var(--teal-deep)" opacity=".6"/>
    <path d="M600 190 C700 150 800 140 964 150 V190Z" fill="var(--teal)"/>
    <path d="M900 0 H964 V120 C950 70 930 30 900 0Z" fill="var(--teal)"/>
  </svg>
  <div class="photo" role="img" aria-label="Photo of a woman with long straight brown hair and a man with a textured short haircut"></div>
  <div class="brand">
    <div class="brand-dot"></div>
    <p class="brand-name">Corvane<span>Haircuts &amp; Colors</span></p>
  </div>
  <p class="tagline">WE OFFER THE<span>BEST STYLE IN TOWN</span></p>
  <p class="cta">MAKE AN APPOINTMENT TODAY!</p>
  <p class="phone">555-0142-678</p>
</section>

</body>
</html>
```